Etiketten-Design für nachhaltige Rasur- & Pflegeprodukte
> Wir suchen Verpackung und Etiketten für eine Marke für nachhaltige Rasur- & Pflegeprodukte.
Habedere liebe Designer,
„Habedere“ sagt man bei uns in Bayern, es bedeutet Hallo oder auf Wiedersehen, je nach Gelegenheit. In diesem Fall: Hallo.
Vielleicht kennst du uns schon, wir sind greenpines, wir betreiben einen kleinen Shop für Bartpflege & Rasur unter greenpines-shop.de und wir versuchen uns nun an einem neuen Thema: nachhaltige Rasur- & Pflegeprodukte für Frauen.
Das machen wir unter dem Namen „Sanft“.
Weil die Frage schon oft aufkam: Jawohl, wir haben uns dafür die Beine und die Achseln mit einem Rasierhobel rasiert.
> Zielgruppe.
Wir arbeiten an einer neuen Pflegelinie für Frauen, die sich vorwiegend mit der Rasur und den dazugehörigen Pflegeprodukten beschäftigt. Die Zielgruppe sind vor allem online-affine Frauen aus Deutschland, Österreich und der Schweiz, aber sicher auch europaweit im Alter von 21-45.
> Aufgabenstellung.
Wir sind auf der Suche nach einem Konzept für unsere Produktverpackungen bzw. Etiketten. Bei den Pflegeprodukten verzichten wir bewusst auf eine Umverpackung.
Konkret geplant sind ein Rasierhobel, dafür haben wir eine schöne Umverpackung. Außerdem starten wir mit Rasieröl, Rasierseife und einem After Shave Balsam. Es werden später noch andere Artikel dazukommen, eine Deocreme zum Beispiel.
Rasieröl, Rasiercreme und After Shave Balsam duften nach Orangen, es werden zwei oder drei weitere Duftrichtungen folgen, die eine wird beispielsweise nach Beeren duften, die andere nach Pfirsich und Mango – bitte beachte das bei der Erstellung des Konzeptes, die Unterschiede sollten später auf den ersten Blick erkennbar sein.
Zurück zum Thema Orange: Wir würden den Duft als leicht herben Zitrusduft bezeichnen.
> Die Maße.
• Umverpackung Rasierhobel, weißer Karton (165x90x40mm)
• Rasieröl 30ml (Etikett: 100x46mm)
• Rasiercreme 60ml (Etikett: 156x32mm)
• After Shave Balsam 60ml (Etikett: 156x32mm)
> Zwingend erforderliche Angaben.
Da es sich um Kosmetikprodukte handelt, sind einige Angaben auf dem Label zwingend erforderlich, beispielhaft sollen die folgenden Infos als Platzhalter dienen.
• Hergestellt für Friedrich Lautner e.K. von greenpines, Lindenhofweg 7, 83109 Kolbermoor
• Ingredients: Aqua, Stearic Acid, Cocos Nucifera oil, Glycerin, Potassium Hydroxide, Litsea Cubeba oil, (and) Citrus Sinensis Peel oil, Orbignya Oleifera oil, Sodium Hydroxide, Macadamia ternifolia oil, Talc, Kaolin, Citric Acid, Simmondsia chinensis oil, Maris sal, C.I. 77892 (and) Rad Clay, Citral, Limonene, Linalool, Geraniol
• Platz für einen Barcode
• Rasieröl sind 30ml / 1.01 FL.OZ. ODER Creme & Balsam jeweils 60ml / 2.03 FL. OZ.
Wir haben ein Bild der aktuellen Gefäße beigefügt, es kann aber durchaus sein, dass wir uns noch umen..

```html
<!DOCTYPE html>
<html lang="de">
<head>
<meta charset="utf-8">
<title>Sanft – Rasieröl Etikett und Rasierhobel Verpackung</title>
<link rel="stylesheet" href="https://fonts.googleapis.com/css2?family=Playfair+Display:wght@700;900&family=Courier+Prime&family=Montserrat:wght@300;500;700&family=Homemade+Apple&display=swap">
<style>
  :root {
    --backdrop: #dededd;
    --navy: #2a3150;
    --apricot: #e8a866;
    --tangerine: #e27a2c;
    --ink: #2a3150;
    --carton: #ecebe9;
    --sage: #8aa49f;
    --leaf: #c9d4d1;
    --box-ink: #2b2d2f;
    --box-soft: #6d6f71;
  }
  * { box-sizing: border-box; margin: 0; padding: 0; }
  html, body { width: 1200px; height: 900px; overflow: hidden; }
  body {
    background: var(--backdrop);
    position: relative;
  }

  /* Oil label */
  .oil-label {
    position: absolute;
    left: 250px;
    top: 220px;
    width: 300px;
    height: 440px;
    background: var(--apricot);
    overflow: hidden;
  }
  .oil-label__top {
    position: absolute;
    inset: 0 0 auto 0;
    height: 260px;
    display: block;
  }
  .oil-label__mark {
    position: absolute;
    left: 85px;
    top: 40px;
    width: 130px;
    height: 130px;
    border-radius: 50%;
    background: var(--apricot);
    display: flex;
    align-items: center;
    justify-content: center;
    font-family: "Playfair Display", serif;
    font-weight: 700;
    font-size: 34px;
    color: var(--navy);
  }
  .oil-label__ornament {
    position: absolute;
    right: 14px;
    top: 262px;
    width: 110px;
    height: 110px;
    border-radius: 50%;
    background: radial-gradient(circle, rgba(226,122,44,0.25), rgba(232,168,102,0));
  }
  .oil-label__body {
    position: absolute;
    left: 0;
    right: 0;
    top: 272px;
    text-align: center;
    color: var(--ink);
  }
  .oil-label__product {
    font-family: "Playfair Display", serif;
    font-weight: 900;
    font-size: 26px;
  }
  .oil-label__scent {
    font-family: "Courier Prime", monospace;
    font-size: 21px;
    color: var(--tangerine);
    margin-top: 2px;
  }
  .oil-label__origin {
    font-family: "Homemade Apple", cursive;
    font-size: 11px;
    margin-top: 26px;
  }
  .oil-label__volume {
    font-family: "Courier Prime", monospace;
    font-size: 11px;
    margin-top: 6px;
  }

  /* Razor carton */
  .razor-box {
    position: absolute;
    left: 680px;
    top: 180px;
    width: 270px;
    height: 495px;
    background: var(--carton);
    overflow: hidden;
  }
  .razor-box__leaves {
    position: absolute;
    left: 60px;
    top: 150px;
    width: 210px;
    height: 290px;
    background: linear-gradient(160deg, var(--leaf), rgba(201,212,209,0.4));
    border-radius: 60% 10% 60% 20%;
  }
  .razor-box__mark {
    position: absolute;
    left: 32px;
    top: 36px;
    width: 170px;
    height: 170px;
    border-radius: 50%;
    background: var(--sage);
    display: flex;
    align-items: center;
    justify-content: center;
    font-family: "Montserrat", sans-serif;
    font-weight: 300;
    font-size: 36px;
    color: var(--carton);
  }
  .razor-box__title {
    position: absolute;
    left: 32px;
    top: 300px;
    font-family: "Montserrat", sans-serif;
    font-weight: 700;
    font-size: 19px;
    letter-spacing: 0.5px;
    color: var(--box-ink);
    line-height: 1.15;
  }
  .razor-box__subtitle {
    display: block;
    font-weight: 300;
    color: var(--box-soft);
  }
  .razor-box__tagline {
    position: absolute;
    left: 32px;
    bottom: 36px;
    font-family: "Montserrat", sans-serif;
    font-weight: 500;
    font-size: 9px;
    letter-spacing: 0.3px;
    color: var(--box-ink);
  }
</style>
</head>
<body>

  <section class="oil-label">
    <svg class="oil-label__top" viewBox="0 0 300 260" preserveAspectRatio="none" aria-hidden="true">
      <path d="M0 0 H300 V238 C270 232 250 246 222 240 C196 234 176 250 148 244 C120 238 96 252 66 246 C40 241 20 250 0 246 Z" fill="var(--navy)"/>
    </svg>
    <div class="oil-label__mark">Sanft</div>
    <div class="oil-label__ornament" role="img" aria-label="Dezentes Orangenscheiben-Ornament"></div>
    <div class="oil-label__body">
      <h1 class="oil-label__product">Rasieröl</h1>
      <p class="oil-label__scent">Orange Blossom</p>
      <p class="oil-label__origin">handmade in germany</p>
      <p class="oil-label__volume">30ml / 1.01 FL.OZ</p>
    </div>
  </section>

  <section class="razor-box">
    <div class="razor-box__leaves" role="img" aria-label="Blassgrüne Blattillustration"></div>
    <div class="razor-box__mark">Sanft</div>
    <h2 class="razor-box__title">RASIERHOBEL<span class="razor-box__subtitle">EXTRA SANFT</span></h2>
    <p class="razor-box__tagline">RASIERER FÜR FRAUEN</p>
  </section>

</body>
</html>
```